Web design for Crowdfunding site HopeWingsRally.com

We need a web design for christian crowdfunding website. Here is the challenge: We need responsive layout that is targeted first in iPad size of screen. It should also scale somehow down to iPhone size of screens. Web layout can be about the same size as iPad screen.

Screens should work so that main page scrolls not but only certain part of the screen scrolls and always one "page" at time. We can implement these "scrolls" then later with javascript but now we need only design. The challenge is to create this kind of hybrid website / app look.

Target is at first to raise funds to orphan people needing about $40 per month for their living and education. There is always some organization which takes care of these kids. Later there will be other christian missions included. At first we are looking to find monthly supporters.

You can be as creative as you want :) As you see from the look and feel sector, I am not looking any same traditional look which many "help kids" sites have. I am looking to reach now younger generation and therefore iPad and mobile are the main screen sizes.

Inspirational designs:
- https://example-gallery.test/profiles/studiofernlake/designs/482716?from=%2Fbrowse%2Fxhr%2Fdesigns%3Fcategory%3Dmobile-app-design
- http://www.artpoolhub.test/design/8261047 Clear, simple visuals
- http://www.artpoolhub.test/design/7394215 Header
- http://www.artpoolhub.test/design/6048392 Contrast in the colors, i think is powerfull

Some terms could be: Kids play, kids are learning (in the school). No static posture but living like kids are. I wonder also how we could also add little bit gaming style even though the question is of reali life of real people. Giving should be rewarding.

Target Market(s)

People who want help other people.

Industry/Entity Type

Christian

Number of Pages Required

4 page

Requirements
Must have
• Homepage. Mission page (In my wireframes it was one kid).
Nice to have
• Other pages and some idea how to scroll. 4 pages is no must. If you feel easy, please give first some draft and I give comments on that.

```html
<!DOCTYPE html>
<html lang="en">
<head>
<meta charset="utf-8">
<title>HopeWingsRally – Profile</title>
<link href="https://fonts.googleapis.com/css2?family=Lato:wght@400;700&display=swap" rel="stylesheet">
<style>
  :root {
    --teal: #45c7ad;
    --ink: #1d1d1d;
    --text: #333333;
    --muted: #9a9a9a;
    --panel: #ecebf2;
    --card: #ffffff;
    --avatar: #a9a9a9;
    --dot: #1b73f0;
    --plus: #2ecc56;
    --ring-track: #d8dcdc;
    --ring-box: #eef0f0;
  }
  * { box-sizing: border-box; margin: 0; padding: 0; }
  html, body { width: 901px; height: 1200px; overflow: hidden; }
  body { font-family: "Lato", Arial, sans-serif; color: var(--text); background: #fff; position: relative; }

  .topbar { position: absolute; left: 0; top: 0; width: 901px; height: 76px; background: var(--teal); }
  .topbar__menu { position: absolute; left: 22px; top: 27px; display: flex; align-items: center; gap: 10px; font-size: 16px; font-weight: 700; color: var(--ink); letter-spacing: -0.2px; }
  .topbar__brand { position: absolute; left: 0; right: 0; top: 20px; text-align: center; font-size: 23px; font-weight: 700; color: var(--ink); letter-spacing: 0.5px; }
  .topbar__auth { position: absolute; right: 18px; top: 23px; display: flex; gap: 18px; font-size: 16px; font-weight: 700; color: var(--ink); }

  .hero { position: absolute; left: 0; top: 76px; width: 901px; height: 405px; background: radial-gradient(ellipse at 50% 55%, #8a8278 0%, #b9b2a8 40%, #e9e6e1 80%, #f4f2ef 100%); }
  .hero__caption { position: absolute; left: 244px; top: 0; width: 270px; font-size: 10px; line-height: 14px; color: #222; }
  .band { position: absolute; left: 0; top: 481px; width: 901px; height: 54px; background: var(--teal); }

  .profile { position: absolute; left: 0; top: 535px; width: 901px; height: 630px; background: var(--panel); }
  .profile__avatar { position: absolute; left: 104px; top: 15px; width: 126px; height: 126px; }
  .profile__details { position: absolute; left: 270px; top: 34px; font-size: 13px; line-height: 27px; color: var(--ink); }
  .following { position: absolute; left: 598px; top: 34px; font-size: 13px; color: var(--ink); }
  .following__item { display: flex; align-items: center; gap: 12px; height: 30px; font-size: 13px; margin-left: 0; }
  .following__item:first-of-type { margin-top: 8px; }
  .section-label { position: absolute; font-size: 13px; color: var(--ink); display: flex; align-items: center; gap: 8px; }

  .missions { position: absolute; top: 159px; width: 362px; display: flex; flex-direction: column; gap: 1px; }
  .missions--left { left: 99px; }
  .missions--right { left: 483px; }
  .mission { position: relative; height: 70px; background: var(--card); }
  .mission__avatar { position: absolute; left: 13px; top: 10px; width: 50px; height: 50px; }
  .mission__name { position: absolute; left: 75px; top: 22px; font-size: 12.5px; line-height: 13px; color: var(--ink); }
  .mission__name small { display: block; font-size: 12.5px; }
  .mission__dot { position: absolute; left: 181px; top: 31px; width: 10px; height: 10px; border-radius: 50%; background: var(--dot); }
  .mission__stats { position: absolute; left: 217px; top: 8px; font-size: 8px; line-height: 22px; color: var(--ink); }
  .mission__ring { position: absolute; left: 264px; top: 8px; width: 56px; height: 54px; background: var(--ring-box); }
  .mission__add { position: absolute; left: 332px; top: 25px; width: 20px; height: 20px; }

  .swipe-hint { position: absolute; left: 654px; top: 874px; font-size: 13px; color: var(--ink); display: flex; gap: 20px; align-items: center; }
  .swipe-hint__dots { color: var(--muted); letter-spacing: 2px; margin-right: 14px; }

  .activity { position: absolute; width: 346px; height: 107px; background: var(--card); padding: 12px 12px 0 34px; }
  .activity__dot { position: absolute; left: 14px; top: 18px; width: 10px; height: 10px; border-radius: 50%; background: var(--dot); }
  .activity__time { position: absolute; right: 12px; top: 15px; font-size: 10px; color: var(--muted); }
  .activity__who { font-size: 13px; font-weight: 700; color: var(--ink); line-height: 18px; }
  .activity__title { font-size: 12.5px; font-weight: 700; color: var(--ink); line-height: 18px; }
  .activity__title--plain { font-weight: 400; }
  .activity__body { font-size: 9.5px; line-height: 15px; color: var(--muted); margin-top: 2px; }
  .activity__clip { position: absolute; left: 13px; top: 36px; }
  .activity__angel { position: absolute; left: 32px; top: 56px; width: 42px; height: 42px; }
  .activity__anon { position: absolute; left: 160px; top: 70px; font-size: 10px; color: var(--muted); }

  .footer-rule { position: absolute; left: 0; top: 1165px; width: 901px; height: 1px; background: #8a8a8a; }
  .next-page { position: absolute; right: 8px; top: 1174px; display: flex; align-items: center; gap: 8px; font-size: 16px; font-weight: 700; color: var(--ink); }
</style>
</head>
<body>

<svg width="0" height="0" style="position:absolute">
  <defs>
    <symbol id="person" viewBox="0 0 60 60">
      <circle cx="30" cy="30" r="28" fill="#fff" stroke="#a9a9a9" stroke-width="2.5"/>
      <clipPath id="personClip"><circle cx="30" cy="30" r="26.5"/></clipPath>
      <g clip-path="url(#personClip)" fill="#a9a9a9">
        <ellipse cx="30" cy="25" rx="10" ry="12"/>
        <path d="M8 60 Q10 40 30 38 Q50 40 52 60 Z"/>
      </g>
    </symbol>
    <symbol id="ring" viewBox="0 0 44 44">
      <circle cx="22" cy="22" r="17" fill="none" stroke="#d8dcdc" stroke-width="3"/>
      <path d="M22 5 A17 17 0 1 1 12 35.8" fill="none" stroke="#3cc79f" stroke-width="3"/>
      <text x="22" y="25" text-anchor="middle" font-family="Lato, sans-serif" font-size="8" fill="#b0b0b0">45°</text>
    </symbol>
    <symbol id="plus" viewBox="0 0 20 20">
      <circle cx="10" cy="10" r="10" fill="#2ecc56"/>
      <path d="M10 5v10M5 10h10" stroke="#fff" stroke-width="2.2"/>
    </symbol>
  </defs>
</svg>

<header class="topbar">
  <div class="topbar__menu">
    <svg width="27" height="22" viewBox="0 0 27 22"><rect y="1" width="27" height="3" fill="#1d1d1d"/><rect y="9.5" width="27" height="3" fill="#1d1d1d"/><rect y="18" width="27" height="3" fill="#1d1d1d"/></svg>
    SEE THE MISSIONS
  </div>
  <div class="topbar__brand">HOPEWINGSRALLY</div>
  <nav class="topbar__auth"><span>LOG IN</span><span>SIGN UP</span></nav>
</header>

<section class="hero" role="img" aria-label="Sepia photograph of two smiling children, the younger eating an orange fruit">
  <p class="hero__caption">involvement. We aim at improving small things around their lives and hope for much smaller in return – their happy little smiles :)</p>
</section>
<div class="band"></div>

<main class="profile">
  <svg class="profile__avatar"><use href="#person"/></svg>
  <div class="profile__details">
    <p>Name: MATTHEW MATT</p>
    <p>Username: matt28</p>
  </div>
  <div class="following">
    <p>FOLLOWING</p>
    <div class="following__item"><svg width="26" height="26"><use href="#person"/></svg>Maria,...</div>
    <div class="following__item"><svg width="26" height="26"><use href="#person"/></svg>Maria,...</div>
    <div class="following__item"><svg width="26" height="26"><use href="#person"/></svg>Maria,...</div>
  </div>

  <div class="section-label" style="left:99px;top:143px">MY MISSIONS
    <svg width="14" height="8" viewBox="0 0 14 8"><path d="M1 1l6 6 6-6" fill="none" stroke="#b8b8c4" stroke-width="1.4"/></svg>
  </div>

  <div class="missions missions--left">
    <article class="mission">
      <svg class="mission__avatar"><use href="#person"/></svg>
      <p class="mission__name">Maria, 11y<small>Orphan, Jacob</small></p>
      <span class="mission__dot"></span>
      <div class="mission__stats">$15 raised<br>$20 to go<br>5 angels in</div>
      <div class="mission__ring"><svg width="56" height="54" viewBox="-6 -5 56 54"><use href="#ring" width="44" height="44"/></svg></div>
      <svg class="mission__add"><use href="#plus"/></svg>
    </article>
    <article class="mission">
      <svg class="mission__avatar"><use href="#person"/></svg>
      <p class="mission__name">Matthew, 11y<small>Orphan, Jacob</small></p>
      <div class="mission__stats">$15 raised<br>$20 to go<br>5 angels in</div>
      <div class="mission__ring"><svg width="56" height="54" viewBox="-6 -5 56 54"><use href="#ring" width="44" height="44"/></svg></div>
      <svg class="mission__add"><use href="#plus"/></svg>
    </article>
    <article class="mission">
      <svg class="mission__avatar"><use href="#person"/></svg>
      <p class="mission__name">Maria, 11y<small style="font-size:10px;color:#777">Orphan, Jacob</small></p>
      <span class="mission__dot" style="left:176px"></span>
      <div class="mission__stats">$15 raised<br>$20 to go<br>5 angels in</div>
      <div class="mission__ring"><svg width="56" height="54" viewBox="-6 -5 56 54"><use href="#ring" width="44" height="44"/></svg></div>
      <svg class="mission__add"><use href="#plus"/></svg>
    </article>
  </div>

  <div class="missions missions--right">
    <article class="mission">
      <svg class="mission__avatar"><use href="#person"/></svg>
      <p class="mission__name">Maria, 11y<small>Orphan, Jacob</small></p>
      <div class="mission__ring"><svg width="56" height="54" viewBox="-6 -5 56 54"><use href="#ring" width="44" height="44"/></svg></div>
      <svg class="mission__add"><use href="#plus"/></svg>
    </article>
    <article class="mission">
      <svg class="mission__avatar"><use href="#person"/></svg>
      <p class="mission__name">Matthew, 11y<small>Orphan, Jacob</small></p>
      <div class="mission__stats">$15 raised<br>$20 to go<br>5 angels in</div>
      <div class="mission__ring"><svg width="56" height="54" viewBox="-6 -5 56 54"><use href="#ring" width="44" height="44"/></svg></div>
      <svg class="mission__add"><use href="#plus"/></svg>
    </article>
  </div>

  <div class="swipe-hint" style="top:339px"><span class="swipe-hint__dots">···</span><span>Swipe to</span><span>see more?</span></div>

  <div class="section-label" style="left:99px;top:384px">ACTIVITIES
    <svg width="8" height="14" viewBox="0 0 8 14"><path d="M1 1l6 6-6 6" fill="none" stroke="#b8b8c4" stroke-width="1.4"/></svg>
  </div>

  <article class="activity" style="left:96px;top:405px">
    <span class="activity__dot"></span>
    <span class="activity__time">10:51 AM &nbsp;›</span>
    <svg class="activity__clip" width="12" height="12" viewBox="0 0 12 12"><path d="M9 4L4.5 8.5a1.5 1.5 0 0 1-2-2L7.5 1.5a2.5 2.5 0 0 1 3.5 3.5L6 10" fill="none" stroke="#aaa" stroke-width="1.1"/></svg>
    <p class="activity__who">Maria</p>
    <p class="activity__title">Report</p>
    <p class="activity__body">Half year report.....</p>
  </article>

  <article class="activity" style="left:450px;top:405px">
    <span class="activity__dot"></span>
    <span class="activity__time">10:51 AM &nbsp;›</span>
    <p class="activity__who">Maria</p>
    <p class="activity__title activity__title--plain">Got a new angel</p>
    <svg class="activity__angel" style="top:55px"><use href="#person"/></svg>
    <span class="activity__anon" style="top:67px">Anonymous</span>
  </article>

  <article class="activity" style="left:96px;top:517px">
    <span class="activity__dot"></span>
    <span class="activity__time">10:51 AM &nbsp;›</span>
    <p class="activity__who">Imma Mustard</p>
    <p class="activity__title activity__title--plain">This is and important message</p>
    <p class="activity__body">Lorem ipsum dolor sit amet, sapien etiam, nunc amet dolor ac odio mauris justo. dolor sit amet, sapien etiam, nunc amet dolor ac odio mauris justo Luctus...</p>
  </article>

  <article class="activity" style="left:450px;top:517px">
    <span class="activity__dot"></span>
    <span class="activity__time">10:51 AM &nbsp;›</span>
    <p class="activity__who">Matthew</p>
    <p class="activity__title">Prayer request</p>
    <p class="activity__body">Lorem ipsum dolor sit amet, sapien etiam, nunc amet dolor ac odio mauris justo. dolor sit amet, sapien etiam, nunc amet dolor ac odio mauris justo Luctus...</p>
  </article>
</main>

<div class="footer-rule"></div>
<div class="next-page">NEXT PAGE
  <svg width="16" height="18" viewBox="0 0 16 18"><path d="M2 2l7 7-7 7M8 2l7 7-7 7" fill="none" stroke="#1b5fd0" stroke-width="1.6"/></svg>
</div>

</body>
</html>
```